Brookvane Consulting Business Card Design

Business Card Design for Brookvane Consulting. Brookvane Consulting is a boutique consultancy based in Atlanta, GA., that specializes in marketing strategy, organization planning, and leadership development. We provide solutions for small businesses and startups as well as Vantage 300 companies.

http://brookvaneconsulting.com/

Target Market(s)

We provide solutions for small businesses and startups as well as Vantage 300 companies.

Industry/Entity Type

Consulting

Contact Information for Business Card

Two sided business card with priority on contact information, logo, tag line (Inspiration to Dream More, Do More, Become More)

Colors

Designer to choose colors to be used in the design.

Requirements
Must have
• contact information, logo, tag line (Inspiration to Dream More, Do More, Become More)
• Simple no over communication.
Nice to have
• I would like to see different placements of logo and creative use of both sides of the card
Should not have
• Do not put too much information on the card.

```html
<!DOCTYPE html>
<html lang="en">
<head>
<meta charset="utf-8">
<title>Brookvane Consulting Business Card</title>
<link rel="stylesheet" href="https://fonts.googleapis.com/css2?family=Roboto:wght@400;500;700&family=Roboto+Condensed:wght@700&display=swap">
<style>
  :root {
    --backdrop: #e8e5e0;
    --card-dark: #232323;
    --card-pattern: #262626;
    --card-light: #ffffff;
    --ink: #1c1c1c;
    --ink-soft: #2a2a2a;
    --on-dark: #ffffff;
    --on-dark-muted: #dcdcdc;
  }
  * { box-sizing: border-box; margin: 0; padding: 0; }
  html, body {
    width: 1200px;
    height: 960px;
    overflow: hidden;
    background: var(--backdrop);
    font-family: "Roboto", Arial, sans-serif;
  }
  .canvas { position: relative; width: 1200px; height: 960px; }

  .card {
    position: absolute;
    box-shadow: 0 6px 14px rgba(0,0,0,0.35);
    overflow: hidden;
  }

  /* Front side */
  .card-front {
    left: 318px; top: 96px;
    width: 612px; height: 368px;
    background: var(--card-dark);
  }
  .card-front .texture {
    position: absolute; inset: 0;
    background: linear-gradient(160deg, var(--card-pattern), var(--card-dark));
  }
  .wordmark {
    position: absolute;
    color: var(--on-dark);
    font-family: "Roboto", Arial, sans-serif;
    font-weight: 500;
    white-space: nowrap;
    display: flex;
    align-items: center;
    gap: 12px;
  }
  .wordmark .mark-dot {
    width: 12px; height: 12px;
    border-radius: 50%;
    background: var(--on-dark);
    flex: none;
  }
  .card-front .wordmark {
    left: 0; right: 0; top: 158px;
    justify-content: center;
    font-size: 36px;
  }
  .tagline {
    position: absolute;
    left: 0; right: 0; top: 292px;
    text-align: center;
    color: var(--on-dark-muted);
    font-size: 14.5px;
    letter-spacing: 0.1px;
  }

  /* Back side */
  .card-back {
    left: 320px; top: 494px;
    width: 600px; height: 342px;
    background: var(--card-dark);
  }
  .contact-panel {
    position: absolute;
    left: 0; top: 6px;
    width: 277px; height: 330px;
    background: var(--card-light);
    border-radius: 0 8px 8px 0;
  }
  .contact-panel::after {
    content: "";
    position: absolute;
    left: -4px; top: 8px;
    width: 264px; height: 314px;
    border: 3px solid var(--ink);
  }
  .contact {
    position: absolute;
    left: 29px; top: 100px;
    color: var(--ink);
  }
  .contact .name {
    font-family: "Roboto Condensed", "Arial Narrow", sans-serif;
    font-weight: 700;
    font-size: 20px;
    letter-spacing: 0.2px;
    margin-bottom: 6px;
  }
  .contact .role {
    font-size: 14.5px;
    font-weight: 500;
    line-height: 19px;
    color: var(--ink-soft);
  }
  .contact .details {
    margin-top: 14px;
    font-size: 14px;
    line-height: 19px;
    color: var(--ink-soft);
  }
  .card-back .wordmark {
    left: 277px; right: 0; top: 152px;
    justify-content: center;
    font-size: 28px;
  }
  .card-back .wordmark .mark-dot { width: 10px; height: 10px; }
</style>
</head>
<body>
<main class="canvas">
  <section class="card card-front" aria-label="Card front">
    <div class="texture" role="img" aria-label="Subtle dark woven grid pattern"></div>
    <div class="wordmark"><span class="mark-dot"></span>Brookvane Consulting</div>
    <p class="tagline">Inspiration to Dream More, Do More, Become More</p>
  </section>

  <section class="card card-back" aria-label="Card back">
    <div class="contact-panel">
      <div class="contact">
        <p class="name">DANA WHITFIELD</p>
        <p class="role">Founder<br>Managing Director</p>
        <p class="details">
          P. 424-555-0193<br>
          dana@brookvaneconsulting.com<br>
          www.brookvaneconsulting.com
        </p>
      </div>
    </div>
    <div class="wordmark"><span class="mark-dot"></span>Brookvane Consulting</div>
  </section>
</main>
</body>
</html>
```